FinTech company looking to revamp and expand client-facing interface for our financial models

Pellworth Engines currently has a very simple website that allows clients to interact with our financial models. We are looking to completely redesign the current site and add several extra pages to provide extra functionality. We want the design to have a modern, slick feel, that will work on both a desktop or a tablet. It should be straightforward for clients to move between different pages at any time, and clear from the layout how to interact with the more advanced features. We have included screenshots of existing pages in the attached design brief, as well as sketches of the functionality required by the new pages, but can't provide a direct link to the current site.
Target Market(s)
Professional investors that will be paying to access the interface
Industry/Entity Type
Finance
Number of Pages Required
4 page
Colors
Designer to choose colors to be used in the design.
Look and feel
Each slider illustrates characteristics of the customer's brand and the style your logo design should communicate.

```html
<!DOCTYPE html>
<html lang="en">
<head>
<meta charset="utf-8">
<title>Vantix – Model Dashboard</title>
<link href="https://fonts.googleapis.com/css2?family=Open+Sans:wght@400;600;700&display=swap" rel="stylesheet">
<style>
  :root {
    --backdrop: #555556;
    --surface: #ffffff;
    --canvas: #f5f5f9;
    --ink: #333333;
    --ink-soft: #444444;
    --head: #545454;
    --row-alt: #f5f4f5;
    --rule: #dcdcdc;
    --field-line: #c9c9cc;
    --accent: #0a8fd0;
  }
  * { box-sizing: border-box; margin: 0; padding: 0; }
  html, body { width: 1068px; height: 1200px; overflow: hidden; background: var(--backdrop); }
  body { font-family: "Open Sans", Arial, sans-serif; color: var(--ink); }
  .stage { position: absolute; left: 0; top: 0; width: 1600px; height: 1798px; transform: scale(0.6675); transform-origin: 0 0; }

  .screen { position: absolute; left: 60px; width: 1500px; background: var(--canvas); box-shadow: 0 2px 8px rgba(0,0,0,.25); }
  .screen--models { top: 51px; height: 872px; }
  .screen--sens { top: 974px; height: 776px; }

  .topbar { position: absolute; left: 0; top: 0; width: 100%; height: 92px; background: var(--surface); box-shadow: 0 1px 3px rgba(0,0,0,.06); }
  .brand { position: absolute; left: 52px; top: 22px; font-size: 38px; font-weight: 600; color: var(--accent); letter-spacing: -0.5px; }
  .horizon { position: absolute; top: 34px; height: 28px; line-height: 28px; font-size: 14px; color: var(--ink); }
  .horizon--active { background: var(--accent); color: #fff; padding: 0 10px; }
  .horizon-divider { position: absolute; left: 351px; top: 19px; width: 1px; height: 48px; background: var(--rule); }
  .mainnav { position: absolute; right: 60px; top: 34px; display: flex; gap: 42px; font-size: 18px; font-weight: 700; color: var(--ink-soft); }

  .field-label { position: absolute; font-size: 15px; color: var(--ink-soft); }
  .field-label b { font-size: 17px; font-weight: 700; }
  .field-label--bold { font-weight: 700; font-size: 15px; }
  .field { position: absolute; width: 308px; height: 50px; background: var(--surface); border: 1px solid var(--field-line); font-size: 14px; line-height: 48px; padding-left: 15px; color: var(--ink); }

  .export { position: absolute; left: 1342px; top: 175px; width: 100px; height: 38px; border: 2px solid var(--accent); color: var(--accent); font-size: 14px; font-weight: 700; display: flex; align-items: center; justify-content: center; gap: 8px; background: var(--surface); }

  .grid { position: absolute; left: 52px; width: 1396px; border-collapse: collapse; table-layout: fixed; background: var(--surface); box-shadow: 0 1px 3px rgba(0,0,0,.15); font-size: 15px; color: var(--ink); }
  .grid th { background: var(--head); color: #fff; font-size: 14px; font-weight: 700; height: 54px; text-align: center; border-left: 1px solid #6a6a6a; }
  .grid th:first-child { border-left: none; }
  .grid td { border-left: 1px solid var(--rule); text-align: center; }
  .grid td:first-child { border-left: none; }
  .grid tbody tr:nth-child(even) td { background: var(--row-alt); }
  .grid .cell-text { text-align: left; }

  .grid--models { top: 267px; }
  .grid--models td { vertical-align: top; padding-top: 22px; line-height: 24px; }
  .grid--models td.id { padding-left: 27px; text-align: left; }
  .grid--models td.sector { padding-left: 19px; text-align: left; }
  .grid--models td.time { padding-left: 25px; text-align: left; }
  .grid--models tbody tr:nth-child(1) { height: 84px; }
  .grid--models tbody tr:nth-child(2) { height: 78px; }
  .grid--models tbody tr:nth-child(3) { height: 87px; }
  .grid--models tbody tr:nth-child(4) { height: 78px; }
  .grid--models tbody tr:nth-child(5) { height: 87px; }

  .grid--sens { top: 267px; }
  .grid--sens td { vertical-align: middle; }
  .grid--sens td.factor { padding-left: 27px; text-align: left; }
  .grid--sens td.id { padding-left: 42px; text-align: left; }
  .grid--sens td.sector { padding-left: 46px; text-align: left; }
  .grid--sens tbody tr:nth-child(1) { height: 65px; }
  .grid--sens tbody tr:nth-child(2) { height: 54px; }
  .grid--sens tbody tr:nth-child(3) { height: 63px; }
  .grid--sens tbody tr:nth-child(4) { height: 53px; }
  .grid--sens tbody tr:nth-child(5) { height: 64px; }
  .sort-caret { display: inline-block; margin-left: 12px; vertical-align: middle; }

  .footer { position: absolute; left: 0; bottom: 0; width: 100%; background: var(--surface); font-size: 15px; text-align: center; color: var(--ink); }
  .screen--models .footer { height: 80px; line-height: 80px; }
  .screen--sens .footer { height: 76px; line-height: 80px; }
</style>
</head>
<body>
<div class="stage">

  <section class="screen screen--models">
    <header class="topbar">
      <div class="brand">Vantix</div>
      <span class="horizon horizon--active" style="left:214px">250D</span>
      <span class="horizon" style="left:303px">83D</span>
      <span class="horizon-divider"></span>
      <span class="horizon" style="left:382px">42D</span>
      <nav class="mainnav"><span>MODELS</span><span>SENSITIVITIES</span><span>FAVOURITES</span></nav>
    </header>

    <div class="field-label" style="left:52px;top:142px">QUALITY &nbsp;<b>THRESHOLD</b></div>
    <div class="field" style="left:52px;top:177px">-10</div>
    <div class="field-label" style="left:389px;top:142px"><b>ABS</b> STAT &nbsp;&nbsp;&nbsp;&nbsp;<b>THRESHOLD</b></div>
    <div class="field" style="left:386px;top:177px">-10</div>

    <table class="grid grid--models">
      <colgroup>
        <col style="width:133px"><col style="width:182px"><col style="width:165px"><col style="width:100px">
        <col style="width:113px"><col style="width:100px"><col style="width:112px"><col style="width:104px">
        <col style="width:99px"><col style="width:108px"><col style="width:89px"><col style="width:91px">
      </colgroup>
      <thead><tr><th>I D</th><th>SECTOR</th><th>TIME</th><th>QUALITY</th><th>STAT 1</th><th>STAT 2</th><th>STAT 3</th><th>STAT 4</th><th>STAT 5</th><th>STAT 6</th><th>STAT 7</th><th>STAT 8</th></tr></thead>
      <tbody>
        <tr><td class="id">MODEL 1</td><td class="sector">MATERIALS</td><td class="time">2019-07-03<br>12:15:00.000</td><td>30.2288</td><td>2.01574</td><td>23.305</td><td>-0.149368</td><td>22.3054</td><td>4.63714</td><td>0.945706</td><td>2.81949</td><td>2.60858</td></tr>
        <tr><td class="id">MODEL 2</td><td class="sector">INDUSTRIALS</td><td class="time">2019-07-03<br>12:15:00.000</td><td>30.2288</td><td>2.01574</td><td>23.305</td><td>-0.149368</td><td>22.3054</td><td>4.63714</td><td>0.945706</td><td>2.81949</td><td>2.60858</td></tr>
        <tr><td class="id">MODEL 3</td><td class="sector">CONSUMER<br>DISCRETIONARY</td><td class="time">2019-07-03<br>12:15:00.000</td><td>30.2288</td><td>2.01574</td><td>23.305</td><td>-0.149368</td><td>22.3054</td><td>4.63714</td><td>0.945706</td><td>2.81949</td><td>2.60858</td></tr>
        <tr><td class="id">MODEL 4</td><td class="sector">INFORMATION<br>TECHNOLOGY</td><td class="time">2019-07-03<br>12:15:00.000</td><td>30.2288</td><td>2.01574</td><td>23.305</td><td>-0.149368</td><td>22.3054</td><td>4.63714</td><td>0.945706</td><td>2.81949</td><td>2.60858</td></tr>
        <tr><td class="id">MODEL 5</td><td class="sector">CONSUMER<br>DISCRETIONARY</td><td class="time">2019-07-03<br>12:15:00.000</td><td>30.2288</td><td>2.01574</td><td>23.305</td><td>-0.149368</td><td>22.3054</td><td>4.63714</td><td>0.945706</td><td>2.81949</td><td>2.60858</td></tr>
      </tbody>
    </table>

    <footer class="footer">Copyright ©&nbsp; 2019 All Rights Reserved</footer>
  </section>

  <section class="screen screen--sens">
    <header class="topbar">
      <div class="brand">Vantix</div>
      <span class="horizon horizon--active" style="left:214px">250D</span>
      <span class="horizon" style="left:303px">83D</span>
      <span class="horizon-divider"></span>
      <span class="horizon" style="left:382px">42D</span>
      <nav class="mainnav"><span>MODELS</span><span>SENSITIVITIES</span><span>FAVOURITES</span></nav>
    </header>

    <div class="field-label field-label--bold" style="left:52px;top:142px">STAT 1 THRESHOLD</div>
    <div class="field" style="left:52px;top:173px"></div>
    <div class="field-label field-label--bold" style="left:381px;top:142px">STAT 2 THRESHOLD</div>
    <div class="field" style="left:381px;top:173px"></div>
    <div class="field-label field-label--bold" style="left:710px;top:142px">STAT 3 THRESHOLD</div>
    <div class="field" style="left:710px;top:173px"></div>

    <div class="export">
      <svg width="15" height="15" viewBox="0 0 16 16" fill="none" stroke="currentColor" stroke-width="1.6"><path d="M12 9v5H2V4h5"/><path d="M9 2h5v5"/><path d="M14 2 7 9"/></svg>
      EXPORT
    </div>

    <table class="grid grid--sens">
      <colgroup>
        <col style="width:133px"><col style="width:189px"><col style="width:408px"><col style="width:116px">
        <col style="width:101px"><col style="width:114px"><col style="width:110px"><col style="width:108px"><col style="width:117px">
      </colgroup>
      <thead><tr><th>FACTOR</th><th style="text-align:left;padding-left:44px">ID<svg class="sort-caret" width="10" height="6" viewBox="0 0 10 6"><path d="M0 0h10L5 6z" fill="#fff"/></svg></th><th style="text-align:left;padding-left:48px">SECTOR</th><th>STAT 1</th><th>STAT 2</th><th>STAT 3</th><th>STAT 4</th><th>STAT 5</th><th>STAT 6</th></tr></thead>
      <tbody>
        <tr><td class="factor">MODEL 1</td><td class="id">MODEL 1</td><td class="sector">MATERIALS</td><td>-1.4</td><td>0.1</td><td>-3.1</td><td>0.7</td><td>30.2</td><td>0.9</td></tr>
        <tr><td class="factor">MODEL 1</td><td class="id">MODEL 1</td><td class="sector">MATERIALS</td><td>2.8</td><td>0.1</td><td>-3.1</td><td>0.7</td><td>30.2</td><td>0.9</td></tr>
        <tr><td class="factor">MODEL 1</td><td class="id">MODEL 1</td><td class="sector">MATERIALS</td><td>-3.7</td><td>0.1</td><td>-3.1</td><td>0.7</td><td>30.2</td><td>0.9</td></tr>
        <tr><td class="factor">MODEL 1</td><td class="id">MODEL 1</td><td class="sector">MATERIALS</td><td>2.8</td><td>0.1</td><td>-3.1</td><td>0.7</td><td>30.2</td><td>0.9</td></tr>
        <tr><td class="factor">MODEL 1</td><td class="id">MODEL 1</td><td class="sector">MATERIALS</td><td>0.8</td><td>0.1</td><td>-3.1</td><td>0.7</td><td>30.2</td><td>0.9</td></tr>
      </tbody>
    </table>

    <footer class="footer">Copyright ©&nbsp; 2019 All Rights Reserved</footer>
  </section>

</div>
</body>
</html>
```